Interior Decorating business - Logo & Stationery

"Willowmere Studio" is a newly established interior decorating company, based in Sydney, providing interior decorating, colour consulting and property styling services to residential and commercial clients.

We require a logo and stationery design (double-sided business card, A4 letterhead and with compliments slip (210mm X 95mm))

Letterhead information and with compliments slip:
Address - 9/31-33 Farrowdale St, Penhaven NSW 2047
Phone - (02)9617 4280
Mobile - 0432 581 906
Email - maren@willowmerestudio.com.au
Web - www.willowmerestudio.com.au
ABN - 47832915064

Business Cards should be double sided and are to include;
Maren Holcroft
Director

with email address, mobile number, website as listed above

They also need to include services offered i.e. Interior Decorating, Colour Consulting, Property Styling

Please note that the current content on the website will be updated, so disregard logo and content currently on the website.

Target Market(s)

Target market is two-fold - residential clients (primarily homeowners with pride in their homes) and commerical clients (specifically business owners of retail shops and cafes and property developers)

Industry/Entity Type

Residential

```html
<!DOCTYPE html>
<html lang="en">
<head>
<meta charset="utf-8">
<title>Willowmere Studio – Business Card</title>
<link rel="stylesheet" href="https://fonts.googleapis.com/css2?family=Berkshire+Swash&family=Cabin:wght@600;700&family=Gelasio:wght@400&display=swap">
<style>
  :root {
    --leaf-green: #7aae3e;
    --brick-red: #c5533c;
    --logo-yellow: #f3e02a;
    --ink: #1a1a1a;
    --paper: #ffffff;
  }
  * { margin: 0; padding: 0; box-sizing: border-box; }
  html, body {
    width: 1200px;
    height: 825px;
    overflow: hidden;
    background: var(--paper);
  }
  .canvas {
    position: relative;
    width: 1200px;
    height: 825px;
    background: var(--paper);
  }
  .card {
    position: absolute;
    top: 84px;
    width: 472px;
    height: 285px;
    overflow: hidden;
  }
  .card--front { left: 56px; }
  .card--back { left: 646px; }
  .card__shapes {
    position: absolute;
    inset: 0;
    width: 100%;
    height: 100%;
  }
  .shape--green { fill: var(--leaf-green); }
  .shape--red { fill: var(--brick-red); }

  .wordmark {
    position: absolute;
    font-family: "Cabin", "Gill Sans", sans-serif;
    font-weight: 700;
    color: var(--logo-yellow);
    line-height: 0.95;
    white-space: nowrap;
  }
  .card--front .wordmark {
    left: 348px;
    top: 20px;
    font-size: 20px;
  }
  .card--back .wordmark {
    left: 22px;
    top: 92px;
    font-size: 49px;
  }

  .holder {
    position: absolute;
    left: 40px;
    top: 112px;
    width: 300px;
    text-align: center;
    color: var(--ink);
  }
  .holder__name {
    font-family: "Berkshire Swash", serif;
    font-size: 29px;
    line-height: 1;
  }
  .holder__role {
    font-family: "Berkshire Swash", serif;
    font-size: 15px;
    margin-top: 2px;
    padding-left: 40px;
  }

  .contact {
    position: absolute;
    left: 6px;
    top: 226px;
    list-style: none;
    font-family: "Gelasio", serif;
    font-size: 10.5px;
    line-height: 15px;
    color: var(--ink);
  }

  .services {
    position: absolute;
    right: 6px;
    top: 221px;
    list-style: none;
    text-align: right;
    font-family: "Cabin", "Gill Sans", sans-serif;
    font-weight: 600;
    font-size: 14px;
    line-height: 20px;
    color: var(--paper);
  }
</style>
</head>
<body>
<main class="canvas">

  <section class="card card--front" aria-label="Business card front">
    <svg class="card__shapes" viewBox="0 0 472 285" aria-hidden="true">
      <rect class="shape--red" x="317" y="0" width="155" height="285"/>
      <path class="shape--green" d="M0,24 C90,8 200,0 290,0 C332,2 346,32 341,92 C337,152 327,220 325,285 L0,285 Z"/>
    </svg>
    <div class="wordmark">Willowmere<br>Studio</div>
    <div class="holder">
      <p class="holder__name">Maren Holcroft</p>
      <p class="holder__role">Director</p>
    </div>
    <ul class="contact">
      <li>Mobile: 0432 581 906</li>
      <li>Email: maren@willowmerestudio.com.au</li>
      <li>Web: www.willowmerestudio.com.au</li>
    </ul>
  </section>

  <section class="card card--back" aria-label="Business card back">
    <svg class="card__shapes" viewBox="0 0 472 285" aria-hidden="true">
      <rect class="shape--green" x="319" y="22" width="153" height="263"/>
      <path class="shape--red" d="M0,24 Q0,18 8,18 C110,12 220,6 282,6 C330,6 346,40 341,100 C337,170 327,230 325,285 L0,285 Z"/>
    </svg>
    <div class="wordmark">Willowmere<br>Studio</div>
    <ul class="services">
      <li>Interior Decorating</li>
      <li>Property Styling</li>
      <li>Colour Consulting</li>
    </ul>
  </section>

</main>
</body>
</html>
```